Design a Website for an IT Support Company

We are an IT support company that provides commercial IT support and services to small and medium sized businesses. We are in need of a website to be developed for our business.
We would like to work with someone who is either familiar with the IT field, or has developed a website for an IT support company in the past.
Some examples of designs/layouts that we like:
https://www.veldaworks.example/
http://www.marsbyquill.example/
http://817kq.example/
http://www.olbenstructures.example/
http://www.bykq.example/
I have attached a word document that gives a menu system/page layout format that we would like for our website as well as branch office phone numbers. Our logo is also attached that you can use for your design purposes. We currently do not have copy produced for all of the pages outlined in the word document, but would get this done during the project with the selected designer.
We would like the website to be SEO friendly & fully responsive. We would prefer a Wordpress format, however, we are open to HTML formats as well.

```html
<!DOCTYPE html>
<html lang="en">
<head>
<meta charset="utf-8">
<title>Corvane IT – IT Support Company</title>
<link rel="stylesheet" href="https://fonts.googleapis.com/css2?family=Raleway:wght@500;600;700&family=Roboto:wght@400;500;700&display=swap">
<style>
:root{
  --blue:#0a73c9;
  --blue-bright:#1b8ee3;
  --blue-deep:#0659a8;
  --dark:#1f1f1f;
  --darker:#151515;
  --ink:#1c1c1c;
  --muted:#555;
  --grey-bg:#eeeeee;
  --white:#fff;
}
*{box-sizing:border-box;margin:0;padding:0}
html,body{width:1200px;height:3046px;overflow:hidden}
body{font-family:'Roboto',sans-serif;color:var(--ink);background:var(--white);position:relative}
.abs{position:absolute}
h1,h2,h3,.heading{font-family:'Raleway',sans-serif}

/* top bar */
.topbar{position:absolute;top:0;left:0;width:1200px;height:45px;background:var(--dark)}
.topbar .phone{position:absolute;left:790px;top:11px;color:#fff;font-size:19px;font-weight:500;display:flex;align-items:center;gap:8px}
.topbar .social{position:absolute;left:980px;top:9px;display:flex;gap:8px}
.topbar .social span{width:28px;height:28px;border-radius:50%;border:2px solid var(--blue-bright);display:block}
.topbar .social span:first-child{background:var(--blue-bright)}

/* header */
.header{position:absolute;top:45px;left:0;width:1200px;height:91px;background:#fff}
.brand{position:absolute;left:70px;top:22px;display:flex;align-items:center;gap:12px}
.brand .dot{width:40px;height:40px;border-radius:50%;background:var(--blue)}
.brand .name{font-family:'Raleway',sans-serif;font-weight:700;font-size:34px;color:var(--ink)}
.nav{position:absolute;top:45px;right:80px;display:flex;gap:58px;font-size:16px;font-weight:500}
.nav a{color:var(--ink);text-decoration:none}
.nav a.active{position:relative}
.nav a.active::before{content:"";position:absolute;left:50%;top:-14px;width:8px;height:8px;margin-left:-4px;border-radius:50%;background:var(--blue)}

/* hero */
.hero{position:absolute;top:136px;left:0;width:1200px;height:906px;background:linear-gradient(180deg,var(--blue-bright) 40%,var(--blue-deep) 100%)}
.hero-photo{position:absolute;top:0;left:0;width:1200px;height:544px;background:linear-gradient(180deg,#0b0f1e 0%,#1a2038 45%,#3a3250 75%,#2b2030 100%);clip-path:polygon(0 0,100% 0,100% 85%,50% 100%,0 85%)}
.hero-copy{position:absolute;left:583px;top:138px;color:#fff}
.hero-copy .kicker{font-family:'Raleway',sans-serif;font-size:27px;font-weight:500;letter-spacing:1px}
.hero-copy h1{font-size:56px;font-weight:600;margin-top:4px;line-height:1.05}
.hero-copy p{font-size:20px;line-height:30px;margin-top:14px;width:540px}
.btn{display:inline-block;font-family:'Roboto',sans-serif;font-weight:500;font-size:17px;color:#fff;text-align:center;text-transform:uppercase}
.btn-solid{background:var(--blue)}
.btn-outline{border:2px solid #fff}
.hero .btn-call{position:absolute;left:579px;top:335px;width:166px;height:51px;line-height:51px}
.welcome{position:absolute;left:0;top:595px;width:1200px;text-align:center;color:#fff}
.welcome h2{font-size:44px;font-weight:600}
.welcome p{width:874px;margin:16px auto 0;font-size:14px;line-height:23px}
.welcome .btn{margin-top:30px;width:156px;height:53px;line-height:49px}

/* services */
.services{position:absolute;top:1042px;left:0;width:1200px;height:680px;background:#fff}
.section-title{text-align:center;font-size:44px;font-weight:700;color:var(--ink)}
.section-title span{color:var(--blue)}
.services .section-title{position:absolute;top:46px;width:1200px}
.service{position:absolute;top:135px;width:300px}
.service .icon{position:absolute;top:0;width:184px;height:184px}
.service h3{position:absolute;top:208px;width:184px;text-align:center;font-size:24px;font-weight:600}
.service.cloud h3{color:var(--blue)}
.service ul{position:absolute;top:270px;list-style:none;font-size:14px;line-height:23px;color:var(--muted)}
.service li{padding-left:28px;position:relative}
.service li::before{content:"";position:absolute;left:2px;top:8px;width:8px;height:8px;border-radius:50%;background:var(--blue)}

/* why */
.why{position:absolute;top:1722px;left:0;width:1200px;height:436px;background:linear-gradient(90deg,#1f2a38 0%,#2e3c4e 40%,#18222e 70%,#121a24 100%)}
.why-copy{position:absolute;left:601px;top:64px;width:560px;color:#fff}
.why-copy h2{font-size:44px;font-weight:600}
.why-copy p{font-size:14px;line-height:24px;margin-top:12px}
.why-copy .btn{margin-top:22px;width:156px;height:51px;line-height:51px}

/* testimonial */
.testimonial{position:absolute;top:2158px;left:0;width:1200px;height:410px;background:linear-gradient(180deg,#e4e4e4,#f3f3f3);overflow:hidden}
.testimonial .band{position:absolute;left:532px;top:0;width:168px;height:410px;background:#f6f6f6}
.testimonial .curve{position:absolute;left:-200px;top:342px;width:1600px;height:400px;border-radius:50%;background:#fff}
.client-name{position:absolute;left:0;top:78px;width:1200px;text-align:center;display:flex;justify-content:center;align-items:center;gap:10px;font-weight:700;font-size:20px;color:#444}
.client-name .sq{width:26px;height:26px;background:#d0186f}
.quote{position:absolute;left:165px;top:134px;width:870px;text-align:center;font-size:15px;line-height:23px;color:#444}
.dots{position:absolute;left:0;top:212px;width:1200px;text-align:center;letter-spacing:2px;font-weight:700;color:#444}
.person{position:absolute;left:0;top:246px;width:1200px;text-align:center;font-size:20px;font-weight:700;color:var(--blue)}
.avatar{position:absolute;left:557px;top:294px;width:88px;height:88px;border-radius:50%;border:5px solid #fff;background:linear-gradient(160deg,#c8cfd6,#7a8490);box-shadow:0 2px 6px rgba(0,0,0,.15)}

/* partners */
.partners{position:absolute;top:2568px;left:0;width:1200px;height:132px;background:#fff}
.partner{position:absolute;top:44px;width:150px;margin-left:-75px;text-align:center;font-family:'Roboto',sans-serif;font-weight:700;font-size:28px;color:#2a4f8f}

/* footer */
.footer{position:absolute;top:2700px;left:0;width:1200px;height:285px;background:var(--dark);color:#ddd}
.footer h4{position:absolute;top:48px;font-family:'Raleway',sans-serif;font-size:20px;font-weight:700;color:var(--blue-bright);letter-spacing:.5px}
.foot-brand{position:absolute;left:101px;top:115px;display:flex;align-items:center;gap:10px}
.foot-brand .dot{width:34px;height:34px;border-radius:50%;border:3px solid #fff}
.foot-brand .name{font-family:'Raleway',sans-serif;font-weight:700;font-size:30px;color:#fff}
.foot-social{position:absolute;left:110px;top:173px;display:flex;gap:8px}
.foot-social span{width:40px;height:40px;border-radius:50%;display:block}
.post{position:absolute;left:341px;width:240px;height:64px}
.post .thumb{position:absolute;left:0;top:0;width:65px;height:63px;border:2px solid #ddd;background:linear-gradient(135deg,#2b6fb0,#9cc3e6)}
.post .txt{position:absolute;left:81px;top:0;font-size:14px;line-height:22px;color:#aaa;width:160px}
.post .date{position:absolute;left:81px;top:50px;font-size:12px;color:#fff;white-space:nowrap}
.field{position:absolute;left:609px;width:248px;height:43px;border:1px solid #ccc;color:#fff;font-size:13px;font-style:italic;padding:12px 20px}
.submit{position:absolute;left:753px;top:189px;width:104px;height:49px;line-height:49px;background:var(--blue);color:#fff;font-weight:700;font-size:17px;text-align:center}
.contacts{position:absolute;left:873px;top:86px;list-style:none;font-size:14px;line-height:26px;color:#eee}
.contacts li{display:flex;align-items:center;gap:12px}

.bottom{position:absolute;top:2985px;left:0;width:1200px;height:61px;background:var(--darker);text-align:center;line-height:61px;color:#fff;font-size:13px;font-weight:700}
.bottom span{color:var(--blue-bright)}
</style>
</head>
<body>

<div class="topbar">
  <div class="phone">
    <svg width="22" height="22" viewBox="0 0 24 24"><circle cx="12" cy="12" r="11" fill="none" stroke="#1b8ee3" stroke-width="2"/><path d="M8.5 6.5l2 2-1.2 1.6c.7 1.6 1.9 2.8 3.5 3.5l1.6-1.2 2 2-1.3 1.6c-3.8-.3-7.3-3.8-7.6-7.6z" fill="#1b8ee3"/></svg>
    555-010-4400
  </div>
  <div class="social"><span></span><span></span><span></span><span></span></div>
</div>

<header class="header">
  <div class="brand"><span class="dot"></span><span class="name">Corvane IT</span></div>
  <nav class="nav">
    <a href="#" class="active">Home</a>
    <a href="#">Services</a>
    <a href="#">Why Corvane IT</a>
    <a href="#">Contact</a>
  </nav>
</header>

<section class="hero">
  <div class="hero-photo" role="img" aria-label="Night-time city skyline with lit office towers"></div>
  <div class="hero-copy">
    <div class="kicker">WE ARE AN</div>
    <h1>IT Support Company</h1>
    <p>that provides commercial IT support and services to small and medium sized businesses.</p>
  </div>
  <a class="btn btn-solid btn-call">Call us now</a>
  <div class="welcome">
    <h2>WELCOME TO Corvane IT</h2>
    <p>Lorem Ipsum is simply dummy text of the printing and typesetting industry. Lorem Ipsum has been the industry's standard dummy text ever since the 1500s, when an unknown printer took a galley of type and scrambled it to make a type specimen book. It has survived not only five centuries, but also the leap into electronic typesetting, remaining essentially unchanged. It was popularised in the 1960s with the release of Typeline sheets containing Lorem Ipsum passages, and more recently with desktop publishing software like Folio Layout including versions of Lorem Ipsum.</p>
    <a class="btn btn-outline">Read more</a>
  </div>
</section>

<section class="services">
  <h2 class="section-title">OUR <span>Services</span></h2>

  <div class="service" style="left:152px">
    <svg class="icon" viewBox="0 0 184 184">
      <circle cx="92" cy="92" r="80" fill="none" stroke="var(--blue)" stroke-width="10"/>
      <circle cx="92" cy="92" r="62" fill="#f1f1f1" stroke="#dcdcdc" stroke-width="3"/>
      <g fill="none" stroke="#222" stroke-width="4">
        <ellipse cx="92" cy="72" rx="22" ry="8"/>
        <path d="M70 72v40c0 4 10 8 22 8s22-4 22-8V72M70 86c0 4 10 8 22 8s22-4 22-8M70 99c0 4 10 8 22 8s22-4 22-8"/>
      </g>
    </svg>
    <h3>Data</h3>
    <ul style="left:-36px">
      <li>Managed IT Services</li><li>IT Support &amp; Consulting</li><li>IT Helpdesk Services</li>
      <li>Network Security</li><li>Data Backup &amp; Recovery</li><li>Servers &amp; Virtualization</li>
      <li>Remote Monitoring Services</li><li>Wireless Networking</li>
      <li>Email &amp; Spam Threat Management</li><li>Structured Cabling</li>
    </ul>
  </div>

  <div class="service cloud" style="left:509px">
    <svg class="icon" viewBox="0 0 184 184">
      <circle cx="92" cy="92" r="80" fill="none" stroke="var(--blue)" stroke-width="10"/>
      <circle cx="92" cy="92" r="62" fill="#f1f1f1" stroke="#cfe3f5" stroke-width="3"/>
      <path d="M66 110h52a14 14 0 0 0 0-28 20 20 0 0 0-38-6 16 16 0 0 0-14 34z" fill="none" stroke="#222" stroke-width="4"/>
    </svg>
    <h3>Cloud</h3>
    <ul style="left:-40px">
      <li>Suite Cloud Migrations</li><li>Nimbus Cloud Management Services</li><li>Cloud Migration Services</li>
      <li>Hosted Virtual Servers</li><li>Hosted Telephone Systems</li>
    </ul>
  </div>

  <div class="service" style="left:862px">
    <svg class="icon" viewBox="0 0 184 184">
      <circle cx="92" cy="92" r="80" fill="none" stroke="var(--blue)" stroke-width="10"/>
      <circle cx="92" cy="92" r="62" fill="#f1f1f1" stroke="#dcdcdc" stroke-width="3"/>
      <g stroke="#222" stroke-width="4" stroke-linecap="round">
        <path d="M62 86v12M70 80v24M78 72v40M86 78v28M94 66v52M102 76v32M110 70v44M118 82v20M126 88v8"/>
      </g>
    </svg>
    <h3>Voice</h3>
    <ul style="left:-32px">
      <li>Openline PBX Consulting</li><li>Business Telephone Systems</li><li>Multiple Office Phone Systems</li>
      <li>Lanterna Telephone Systems</li><li>SIP Trunks</li>
    </ul>
  </div>
</section>

<section class="why" role="img" aria-label="Two colleagues reviewing a tablet in a dim office">
  <div class="why-copy">
    <h2>WHY Corvane IT</h2>
    <p>Lorem Ipsum is simply dummy text of the printing and typesetting industry. Lorem Ipsum has been the industry's standard dummy text ever since the 1500s, when an unknown printer took a galley of type and scrambled it to make a type specimen book. It has survived not only five centuries, but also the leap into electronic typesetting, remaining essentially unchanged. It was popularised in the 1960s with the release of Typeline sheets containing Lorem Ipsum passages, and more recently with desktop publishing software like Folio Layout including versions of Lorem Ipsum.</p>
    <a class="btn btn-solid">Read more</a>
  </div>
</section>

<section class="testimonial">
  <div class="band"></div>
  <div class="curve"></div>
  <div class="client-name"><span class="sq"></span>Halden Marsh</div>
  <p class="quote">" Lorem Ipsum is simply dummy text of the printing and typesetting industry. Lorem Ipsum has been the industry's standard dummy text ever since the 1500s, when an unknown printer took a galley of type and scrambled it to make a type specimen book. "</p>
  <div class="dots">..........</div>
  <div class="person">Marcus Ellery</div>
  <div class="avatar" role="img" aria-label="Portrait of the client contact"></div>
</section>

<section class="partners">
  <div class="partner" style="left:170px;color:#c0392b">oriel</div>
  <div class="partner" style="left:351px;color:#b01e2b">Brevik</div>
  <div class="partner" style="left:526px;color:#1d2b5c">TALO</div>
  <div class="partner" style="left:698px;color:#0a64b4">Quenra</div>
  <div class="partner" style="left:869px;color:#1b3f8f">vantor</div>
  <div class="partner" style="left:1039px;color:#22307a">NEXIL</div>
</section>

<footer class="footer">
  <div class="foot-brand"><span class="dot"></span><span class="name">Corvane IT</span></div>
  <div class="foot-social">
    <span style="background:#3b5a9a"></span><span style="background:#27a9e1"></span><span style="background:#d6422f"></span><span style="background:#0b7bc1"></span>
  </div>

  <h4 style="left:345px">BLOG POSTS</h4>
  <div class="post" style="top:85px">
    <div class="thumb" role="img" aria-label="Blog post thumbnail"></div>
    <div class="txt">Lorem Ipsum is simply dummy text of</div>
    <div class="date">Today 5.60 pm - 12.06.2014</div>
  </div>
  <div class="post" style="top:172px">
    <div class="thumb" role="img" aria-label="Blog post thumbnail"></div>
    <div class="txt">Lorem Ipsum is simply dummy text of</div>
    <div class="date">Today 5.60 pm - 12.06.2014</div>
  </div>

  <h4 style="left:609px">NEWSLETTER</h4>
  <div class="field" style="top:85px">Name</div>
  <div class="field" style="top:138px">Email</div>
  <div class="submit">SUBMIT</div>

  <h4 style="left:873px">CONTACT US</h4>
  <ul class="contacts">
    <li><svg width="14" height="14" viewBox="0 0 24 24"><path d="M5 2l5 5-3 3c1.5 3 4 5.5 7 7l3-3 5 5-3 3C10 21 3 14 2 5z" fill="#1b8ee3"/></svg>Main Number: 555-010-4400</li>
    <li><svg width="14" height="14" viewBox="0 0 24 24"><path d="M5 2l5 5-3 3c1.5 3 4 5.5 7 7l3-3 5 5-3 3C10 21 3 14 2 5z" fill="#1b8ee3"/></svg>Houston: 555-010-4410</li>
    <li><svg width="14" height="14" viewBox="0 0 24 24"><path d="M5 2l5 5-3 3c1.5 3 4 5.5 7 7l3-3 5 5-3 3C10 21 3 14 2 5z" fill="#1b8ee3"/></svg>San Antonio: 555-010-4420</li>
    <li><svg width="14" height="14" viewBox="0 0 24 24"><path d="M5 2l5 5-3 3c1.5 3 4 5.5 7 7l3-3 5 5-3 3C10 21 3 14 2 5z" fill="#1b8ee3"/></svg>Austin: 555-010-4430</li>
    <li><svg width="14" height="14" viewBox="0 0 24 24"><path d="M5 2l5 5-3 3c1.5 3 4 5.5 7 7l3-3 5 5-3 3C10 21 3 14 2 5z" fill="#1b8ee3"/></svg>Tulsa: 555-010-4440</li>
    <li><svg width="14" height="14" viewBox="0 0 24 24"><path d="M5 2l5 5-3 3c1.5 3 4 5.5 7 7l3-3 5 5-3 3C10 21 3 14 2 5z" fill="#1b8ee3"/></svg>Oklahoma City: 555-010-4450</li>
  </ul>
</footer>

<div class="bottom">© <span>Corvane IT</span> - 2017. All Rights Reserved.</div>

</body>
</html>
```